Harbourline Electrical Solutions

On one side. LOGO (underneath:) Commercial Industrial Residential

- NAME & CONTACT DETAILS

Marcus T. Hollings
Project Manager

(Cell icon) (441) 555-0187
(Email icon) hlelectricalsolutions@mailvento.com
(Facebook & Instagram icons )@hlelectricalsolutions

Other side: LOGO - underneath ELECTRICAL CONSTRUCTION & MAINTENANCE . LED LIGHTING & AUTOMATION . LIFE SAFETY SYSTEMS (FIRE ALARM / SECURITY) . DATA & COMMUNICATION

```html
<!DOCTYPE html>
<html lang="en">
<head>
<meta charset="utf-8">
<title>Harbourline Electrical Solutions – Business Card</title>
<link rel="stylesheet" href="https://fonts.googleapis.com/css2?family=Montserrat:wght@500;600;700&family=Open+Sans:wght@400;600&display=swap">
<style>
  :root {
    --page-bg: #e4e5e7;
    --card-dark: #4b4c4f;
    --card-dark-ink: #8e9094;
    --card-dark-ink-strong: #2f3033;
    --card-light: #ffffff;
    --teal: #1c6478;
    --teal-band: #2a7d93;
    --ink: #3c3d40;
    --ink-soft: #6b6d71;
    --white: #ffffff;
  }
  * { box-sizing: border-box; margin: 0; padding: 0; }
  html, body {
    width: 1200px; height: 960px; overflow: hidden;
    background: var(--page-bg);
    font-family: "Open Sans", Arial, sans-serif;
  }
  .canvas {
    position: relative; width: 1200px; height: 960px;
    display: flex; flex-direction: column; align-items: center;
    justify-content: center; gap: 40px;
  }
  .card {
    position: relative; width: 700px; height: 400px;
    box-shadow: 0 10px 24px rgba(0,0,0,.18);
    overflow: hidden;
  }

  /* ---------- back side ---------- */
  .card--back { background: var(--card-dark); }
  .back-brand {
    position: absolute; left: 150px; top: 110px;
    display: flex; align-items: center; gap: 20px;
  }
  .brand-square {
    width: 64px; height: 64px; background: var(--card-dark-ink-strong);
  }
  .back-brand .brand-divider {
    width: 1px; height: 96px; background: var(--card-dark-ink);
  }
  .back-brand .brand-name {
    font-family: "Montserrat", Arial, sans-serif; font-weight: 500;
    font-size: 30px; line-height: 1.1; letter-spacing: 3px;
    text-transform: uppercase; color: var(--card-dark-ink);
  }
  .services {
    position: absolute; left: 60px; right: 60px; top: 270px;
    font-family: "Montserrat", Arial, sans-serif; font-weight: 500;
    font-size: 17px; line-height: 1.55; color: var(--card-dark-ink-strong);
    text-align: center;
  }

  /* ---------- front side ---------- */
  .card--front { background: var(--card-light); }
  .front-brand {
    position: absolute; left: 48px; top: 150px;
  }
  .front-brand .brand-lockup { display: flex; align-items: center; gap: 14px; }
  .front-brand .brand-divider { width: 1px; height: 70px; background: var(--teal); }
  .front-brand .brand-name {
    font-family: "Montserrat", Arial, sans-serif; font-weight: 600;
    font-size: 20px; line-height: 1.12; letter-spacing: 2px;
    text-transform: uppercase; color: var(--teal);
  }
  .front-brand .brand-square { width: 44px; height: 44px; background: var(--teal); }
  .sectors {
    margin-top: 14px;
    font-family: "Montserrat", Arial, sans-serif; font-weight: 500;
    font-size: 13.5px; letter-spacing: 1px; color: var(--ink);
    text-transform: uppercase;
  }
  .contact {
    position: absolute; left: 380px; top: 110px;
  }
  .contact .person-name {
    font-family: "Montserrat", Arial, sans-serif; font-weight: 700;
    font-size: 24px; letter-spacing: .5px; color: var(--teal);
    text-transform: uppercase;
  }
  .contact .person-role {
    font-family: "Montserrat", Arial, sans-serif; font-weight: 600;
    font-size: 15px; color: var(--ink); margin-top: 2px;
  }
  .contact-list { list-style: none; margin-top: 20px; }
  .contact-list li {
    display: flex; align-items: center; gap: 10px;
    font-size: 14.5px; color: var(--ink-soft); margin-bottom: 6px;
  }
  .contact-list svg { width: 16px; height: 16px; flex: none; }
  .social-band {
    position: absolute; right: 0; bottom: 0; width: 330px; height: 46px;
  }
  .social-band svg.band-shape { position: absolute; inset: 0; width: 100%; height: 100%; }
  .social-band .handle {
    position: absolute; left: 44px; top: 0; height: 46px;
    display: flex; align-items: center; gap: 10px;
    color: var(--white); font-size: 15px; font-weight: 600;
  }
  .social-dot { width: 14px; height: 14px; border-radius: 50%; background: var(--white); }
</style>
</head>
<body>
<main class="canvas">

  <section class="card card--back" aria-label="Card back">
    <div class="back-brand">
      <span class="brand-square" aria-hidden="true"></span>
      <span class="brand-divider" aria-hidden="true"></span>
      <p class="brand-name">Harbourline<br>Electrical<br>Solutions</p>
    </div>
    <p class="services">
      Electrical Construction &amp; Maintenance • LED Lighting &amp; Automation<br>
      Life Safety Systems (Fire Alarm / Security) • Data &amp; Communication
    </p>
  </section>

  <section class="card card--front" aria-label="Card front">
    <div class="front-brand">
      <div class="brand-lockup">
        <span class="brand-square" aria-hidden="true"></span>
        <span class="brand-divider" aria-hidden="true"></span>
        <p class="brand-name">Harbourline<br>Electrical<br>Solutions</p>
      </div>
      <p class="sectors">Commercial • Industrial • Residential</p>
    </div>

    <div class="contact">
      <h1 class="person-name">Marcus T. Hollings</h1>
      <p class="person-role">Project Manager</p>
      <ul class="contact-list">
        <li>
          <svg viewBox="0 0 16 16" aria-hidden="true"><rect x="4" y="1" width="8" height="14" rx="1.5" fill="none" stroke="#1c6478" stroke-width="1.6"/><line x1="7" y1="12.5" x2="9" y2="12.5" stroke="#1c6478" stroke-width="1.4"/></svg>
          (441) 555-0187
        </li>
        <li>
          <svg viewBox="0 0 16 16" aria-hidden="true"><rect x="1" y="3.5" width="14" height="9" fill="#1c6478"/><polyline points="1,3.5 8,9 15,3.5" fill="none" stroke="#ffffff" stroke-width="1.3"/></svg>
          hlelectricalsolutions@mailvento.com
        </li>
      </ul>
    </div>

    <div class="social-band">
      <svg class="band-shape" viewBox="0 0 330 46" preserveAspectRatio="none" aria-hidden="true">
        <polygon points="10,0 330,0 330,46 0,46" fill="#2a7d93"/>
      </svg>
      <p class="handle"><span class="social-dot" aria-hidden="true"></span>@hlelectricalsolutions</p>
    </div>
  </section>

</main>
</body>
</html>
```